CREATE A BUSINESS CARD FOR A BOAT CLEANING SERVICE

WE ARE STARTING A NEW BOAT CLEANING BUSINESS. WE DIVE UNDERWATER TO CLEAN BOAT HULLS, JETTIES, UNDERWATER STRUCTURES ETC. WE ARE LOOKING FOR AN UPPERMARKET MODERN LOGO AND BUSINESS CARD AS ALOT OF OUR TARGET MARKET WILL BE HIGH END. YOU HAVE TO DESIGN A BUSINESS CARD AND LOGO SEPERATELY .
THE BUSINESS CARD DIMESNION MUST BE STANDARD SIZE.
The standard dimensions of a printed business card are 3.5 x 2 inches

Target Market(s)

UNDERWATER SERVICED

Industry/Entity Type

Business

Contact Information for Business Card

HOLLAND UNDERWATER SERVICES

Font styles to use
Serif

Colors

Designer to choose colors to be used in the design.

Requirements
Must have
• HOLLAND
Nice to have
• dark
Should not have
• more than 3 colors

```html
<!DOCTYPE html>
<html lang="en">
<head>
<meta charset="utf-8">
<title>Holland Underwater Services – Business Card</title>
<link rel="stylesheet" href="https://fonts.googleapis.com/css2?family=Open+Sans:wght@400;600&display=swap">
<style>
  :root {
    --canvas: #e8e9eb;
    --slate: #797979;
    --navy: #15508b;
    --white: #ffffff;
  }
  * { box-sizing: border-box; margin: 0; padding: 0; }
  html, body {
    width: 1200px; height: 900px; overflow: hidden;
    background: var(--canvas);
  }
  .stage { position: relative; width: 1200px; height: 900px; }

  .card { position: absolute; overflow: hidden; box-shadow: 0 6px 18px rgba(0,0,0,.18); }

  /* Front */
  .card-front {
    left: 77px; top: 34px; width: 588px; height: 363px;
    background: var(--slate); color: var(--white);
    font-family: "Open Sans", Arial, sans-serif;
  }
  .card-front .waves { position: absolute; inset: 0; }
  .holder { position: absolute; left: 31px; top: 45px; }
  .holder-name { font-weight: 600; font-size: 19px; letter-spacing: .2px; line-height: 1.2; }
  .holder-role { font-size: 15px; line-height: 1.3; }

  .contact-list { position: absolute; left: 31px; top: 155px; list-style: none; }
  .contact-list li {
    display: flex; align-items: center; gap: 8px;
    font-size: 15px; line-height: 21.5px;
  }
  .contact-list svg { width: 11px; height: 11px; fill: var(--white); flex: none; }

  .address {
    position: absolute; left: 0; right: 0; top: 311px;
    text-align: center; font-size: 15px;
  }

  /* Company name, set in the card's text face */
  .company-name {
    position: absolute; text-align: center;
    font-family: "Open Sans", Arial, sans-serif; font-weight: 600;
    line-height: 1.2;
  }
  .card-front .company-name {
    left: 300px; top: 70px; width: 250px;
    font-size: 28px; color: var(--white);
  }

  /* Back */
  .card-back {
    left: 388px; top: 505px; width: 567px; height: 352px;
    background: var(--white);
  }
  .card-back .company-name {
    left: 0; right: 0; top: 118px; margin: 0 auto; width: 300px;
    font-size: 32px; color: var(--navy);
  }
</style>
</head>
<body>
<main class="stage">

  <section class="card card-front" aria-label="Business card front">
    <svg class="waves" viewBox="0 0 588 363" preserveAspectRatio="none" aria-hidden="true">
      <path d="M0 293 C170 248 420 296 588 198 L588 363 L0 363 Z" fill="#ffffff"/>
      <path d="M0 300 C200 268 440 304 588 212 L588 363 L0 363 Z" fill="#15508b"/>
    </svg>

    <div class="holder">
      <p class="holder-name">MARCUS BRENNAN</p>
      <p class="holder-role">Managing Director</p>
    </div>

    <ul class="contact-list">
      <li>
        <svg viewBox="0 0 24 24"><path d="M6.6 10.8a15.1 15.1 0 0 0 6.6 6.6l2.2-2.2a1 1 0 0 1 1-.25 11.4 11.4 0 0 0 3.6.57 1 1 0 0 1 1 1V20a1 1 0 0 1-1 1A17 17 0 0 1 3 4a1 1 0 0 1 1-1h3.5a1 1 0 0 1 1 1c0 1.25.2 2.45.57 3.57a1 1 0 0 1-.25 1z"/></svg>
        (044)123456789
      </li>
      <li>
        <svg viewBox="0 0 24 24"><path d="M2 5h20v2l-10 7L2 7z"/><path d="M2 9l10 7 10-7v10H2z"/></svg>
        info@youremail.com
      </li>
      <li>
        <svg viewBox="0 0 24 24"><circle cx="12" cy="12" r="10"/><path d="M2 12h20M12 2c3 3 3 17 0 20M12 2c-3 3-3 17 0 20" stroke="#797979" stroke-width="1.6" fill="none"/></svg>
        www.websitename.com
      </li>
    </ul>

    <p class="company-name">Holland Underwater Services</p>

    <p class="address">1234, Address GoesHere, Country name, 12345</p>
  </section>

  <section class="card card-back" aria-label="Business card back">
    <p class="company-name">Holland Underwater Services</p>
  </section>

</main>
</body>
</html>
```